Revamp Of Landing Page For an Automated AI Voice Agents Agency

here is my current landing page https://app.brightfernpromotionhub.biz/v2/preview/WXKRPmQ4hLzYBvNdTeGS?notrack=true

Please use all my current content and imagery of ai agents in your new design. Make it easy to ready, easy to navigate and easy to understand

I am looking for a SLEEK shiny polished looking website. I like Dark themed sites but am open to see light themed sites too so please dont be shy.

The site should have an Ai Voice Agent Theme about it. Maybe look and feel of futureistic but simple and not intimidating to the average person...

Here are a couple website designs I like for reference:
https://q7v.io/
https://ai-bots.marekholvin.com/
https://chatwelmo.com/ai-agents

Target Market(s)

b2b

Industry/Entity Type

AI Voice Agents

Coding

Coded - Design and coding required

Font styles to use
Other font styles liked:
• open

Requirements
Must have
• all elements and content and images used in existing design.
Nice to have
• open
Should not have
• open

```html
<!DOCTYPE html>
<html lang="en">
<head>
<meta charset="utf-8">
<title>Brightfern Promotion Hub — AI Voice Agents</title>
<link href="https://fonts.googleapis.com/css2?family=Playfair+Display:wght@700;800&family=Poppins:wght@400;500;600;700&display=swap" rel="stylesheet">
<style>
:root{
  --night:#12052e;
  --deep:#1f0a4d;
  --violet:#3b13a0;
  --purple:#7b2ff7;
  --magenta:#c84bd6;
  --orange:#f7a04b;
  --gold:#f4b64a;
  --ink:#1b1030;
  --white:#ffffff;
  --soft:#e9ddff;
  --grey:#5c5470;
}
*{box-sizing:border-box;margin:0;padding:0}
html,body{width:1200px;height:5343px;overflow:hidden}
body{position:relative;font-family:"Poppins",sans-serif;background:var(--white);color:var(--ink)}
.abs{position:absolute}
.center{left:0;width:1200px;text-align:center}
.serif{font-family:"Playfair Display",serif;font-weight:800;text-transform:uppercase;letter-spacing:-.5px}
.grad-gold{background:linear-gradient(90deg,#f0a24a,#f7c06a);-webkit-background-clip:text;background-clip:text;color:transparent}
.grad-purple{background:linear-gradient(90deg,#b98cff,#f0b6d8);-webkit-background-clip:text;background-clip:text;color:transparent}
.btn{position:absolute;left:458px;width:284px;height:52px;border-radius:26px;border:2px solid #f2a75c;
  background:linear-gradient(90deg,var(--purple),var(--magenta) 60%,var(--orange));color:#fff;font-size:13px;font-weight:600;
  display:flex;align-items:center;justify-content:center;gap:8px;text-transform:uppercase}
.btn i{width:14px;height:14px;border-radius:50%;background:#fff;display:inline-block;position:relative}
.btn i:after{content:"";position:absolute;left:4px;top:4px;width:4px;height:4px;border-top:2px solid var(--magenta);border-right:2px solid var(--magenta);transform:rotate(45deg)}
.copy{font-size:13.5px;line-height:24px}

/* logo */
.brand{position:absolute;display:flex;align-items:center;gap:12px;left:0;width:1200px;justify-content:center}
.brand .dot{width:34px;height:34px;border-radius:50%;background:var(--purple)}
.brand span{font-family:"Poppins",sans-serif;font-weight:600;font-size:24px;color:#b06cf2}

/* hero */
.hero{top:0;left:0;width:1200px;height:1260px;background:radial-gradient(ellipse at 50% 40%,#4a17a6 0%,#2a0b6b 45%,#16063a 100%)}
.hero h1{top:130px;font-size:54px;color:#fff}
.brain{left:486px;top:290px;width:228px;height:228px;border-radius:50%;border:3px solid #d5548e;
  background:radial-gradient(circle,#ff8a5b 0%,#c2327a 35%,#3a0f8a 75%)}
.wave{left:170px;top:360px;width:860px;height:90px;background:linear-gradient(90deg,transparent,rgba(240,120,120,.45),transparent);border-radius:50%}
.feat{position:absolute;width:200px;text-align:center;color:#fff;font-size:13.5px;font-weight:500}
.feat .ic{width:48px;height:48px;border-radius:50%;background:#fff;margin:0 auto 8px;display:flex;align-items:center;justify-content:center}
.hero h2{top:612px;font-size:28px;font-weight:600;color:#fff}
.hero .copy{top:664px;color:#fff}
.dots{left:0;top:880px;width:1200px;height:380px;background:radial-gradient(ellipse at 50% 60%,rgba(210,80,200,.55),transparent 65%)}
.workforce{top:905px;font-size:46px;line-height:58px}

/* carousel */
.card{position:absolute;border-radius:8px;border:3px solid #f2b25c;background:linear-gradient(160deg,#2b2f5a,#0c1028)}
.card.light{background:linear-gradient(160deg,#e8e2dc,#8b7a6b)}
.card.face{background:linear-gradient(160deg,#3a4a6a,#121a30)}
.label{position:absolute;font-size:12.5px;font-weight:700;text-transform:uppercase;color:var(--ink);text-align:center}
.arrow{position:absolute;width:52px;height:52px;border-radius:50%;display:flex;align-items:center;justify-content:center}
.sales h3{top:1447px;font-size:20px;font-weight:600;color:var(--ink)}
.sales .copy{color:var(--grey);font-size:13px;line-height:22px}

/* wish */
.wish{top:1810px;left:0;width:1200px;height:524px;background:linear-gradient(90deg,#1a0a4a,#14063a 55%,#10042e)}
.wish .visual{left:0;top:0;width:620px;height:524px;background:radial-gradient(ellipse at 40% 50%,#6b4ad6 0%,#3a1f8a 40%,transparent 75%)}
.wish h2{left:636px;top:1900px;font-size:44px;line-height:56px;color:#fff}
.wish-sub{left:636px;top:2050px;font-size:20px;font-weight:700;line-height:30px;color:#fff}
.wish-copy{left:636px;top:2130px;width:460px;font-size:13.5px;line-height:24.5px;color:#fff}

/* benefits */
.sick{top:2393px;font-size:44px;color:var(--ink)}
.rule{left:370px;top:2467px;width:460px;height:3px;background:linear-gradient(90deg,transparent,#8a8aa8,transparent)}
.orb{position:absolute;width:290px;height:290px;border-radius:50%;background:radial-gradient(circle at 50% 35%,#2a1266,#12052e);
  color:#fff;text-align:center;padding-top:58px}
.orb.mid{background:linear-gradient(135deg,var(--purple),var(--magenta) 55%,var(--orange))}
.orb h4{font-size:15px;font-weight:600;text-transform:uppercase;margin-top:10px}
.orb hr{width:60px;border:0;border-top:2px solid #fff;margin:10px auto}
.orb p{font-size:11.5px;line-height:22px;width:160px;margin:0 auto}

/* hire */
.hire{left:112px;top:2921px;width:976px;height:458px;border-radius:10px;background:linear-gradient(180deg,#1d0a40,#120630)}
.hire-h{top:2978px;font-size:44px;line-height:56px}
.hire-sub{top:3106px;font-size:20px;font-weight:600;color:#d9659a}
.hire-line{top:3138px;font-size:20px;font-weight:600;color:#fff}

/* faq */
.faq-h{top:3462px;font-size:44px;color:var(--ink)}
.faq{position:absolute;left:197px;width:806px;height:68px;border-radius:34px;background:linear-gradient(90deg,#ddd0ff,#fde8d8);
  display:flex;align-items:center;justify-content:space-between;padding:0 18px 0 28px;font-size:15px;font-weight:600;color:var(--ink)}
.faq b{width:50px;height:50px;border-radius:50%;background:var(--deep);display:flex;align-items:center;justify-content:center}

/* reviews */
.lower{top:4100px;left:0;width:1200px;height:859px;background:linear-gradient(180deg,#1c0a4a,#2b0f70 60%,#1a0848)}
.review{left:112px;top:3891px;width:976px;height:438px;background:linear-gradient(90deg,#6a2cf5,#c548d2 55%,#f5a24f);border:2px solid #f6d2a8}
.review h2{top:3950px;font-family:"Playfair Display",serif;font-weight:700;font-size:38px;line-height:52px;color:#fff}
.stars{top:4128px;font-size:30px;color:var(--gold);letter-spacing:2px}
.robot{left:490px;top:4208px;width:228px;height:250px;border-radius:48% 48% 40% 40%;background:radial-gradient(circle at 50% 35%,#ffffff,#c9ccd8 55%,rgba(80,90,140,.6))}
.possible{top:4526px;font-size:46px;line-height:58px;color:#fff}

/* footer */
.foot-text{top:5098px;font-size:17px;line-height:29px;color:var(--ink)}
.foot-links{top:5174px;font-size:12px;font-weight:500;color:var(--ink)}
.foot-rule{left:0;top:5214px;width:1200px;height:1px;background:#e4e0ec}
.copyright{top:5236px;font-size:12px;font-weight:500;color:var(--ink)}
</style>
</head>
<body>

<section class="abs hero" aria-label="Hero">
  <div class="abs dots" role="img" aria-label="Glowing dotted wave pattern"></div>
</section>
<div class="brand" style="top:52px"><div class="dot"></div><span>Brightfern Promotion Hub</span></div>
<h1 class="abs center serif hero-title" style="top:130px;font-size:54px;color:#fff">AI Voice Agents That <span class="grad-gold">Can</span></h1>
<div class="abs wave" role="img" aria-label="Sound wave glow"></div>
<div class="abs brain" role="img" aria-label="Glowing AI brain illustration"></div>

<div class="feat" style="left:294px;top:256px"><div class="ic"><svg width="24" height="24" viewBox="0 0 24 24" fill="none" stroke="#3b13a0" stroke-width="2"><path d="M5 4h4l2 5-2.5 1.5a11 11 0 005 5L15 13l5 2v4a2 2 0 01-2 2A16 16 0 013 6a2 2 0 012-2"/></svg></div>Transfer Calls</div>
<div class="feat" style="left:758px;top:258px"><div class="ic"><svg width="24" height="24" viewBox="0 0 24 24" fill="none" stroke="#3b13a0" stroke-width="2"><circle cx="12" cy="12" r="8"/><path d="M9 12h6M12 9v6"/></svg></div>Answer Calls</div>
<div class="feat" style="left:58px;top:370px"><div class="ic"><svg width="24" height="24" viewBox="0 0 24 24" fill="none" stroke="#3b13a0" stroke-width="2"><path d="M6 16V11a6 6 0 0112 0v5l2 2H4zM10 20h4"/></svg></div>Follow Up with Reminders</div>
<div class="feat" style="left:940px;top:360px"><div class="ic"><svg width="24" height="24" viewBox="0 0 24 24" fill="none" stroke="#3b13a0" stroke-width="2"><rect x="4" y="5" width="16" height="15" rx="2"/><path d="M4 10h16M9 14h2M13 14h2M9 17h2"/></svg></div>Book Appointments</div>
<div class="feat" style="left:217px;top:506px"><div class="ic"><svg width="24" height="24" viewBox="0 0 24 24" fill="none" stroke="#3b13a0" stroke-width="2"><rect x="3" y="6" width="18" height="12" rx="2"/><path d="M3 7l9 6 9-6"/></svg></div>Send Text Messages</div>
<div class="feat" style="left:752px;top:458px"><div class="ic"><svg width="24" height="24" viewBox="0 0 24 24" fill="none" stroke="#3b13a0" stroke-width="2"><rect x="3" y="6" width="18" height="12" rx="2"/><path d="M3 7l9 6 9-6"/></svg></div>Send Emails</div>

<h2 class="abs center" style="top:612px;font-size:28px;font-weight:600;color:#fff">Available 24 Hours, 7 Days a Week!</h2>
<p class="abs center copy" style="top:664px;color:#fff">We Will Create An Ai Agent Customized For Your Business At No Cost. Simply Click The Button<br>Above And Your Very Own Ai Agent Will Be Calling You In Just A Couple Minutes. Experience The<br>Magic And Get Ready To Be Very Impressed!</p>
<a class="btn" style="top:764px">Get An Instant Free Demo <i></i></a>

<h2 class="abs center serif workforce grad-purple" style="top:905px;font-size:46px;line-height:58px">Meet Your New AI–<br>Powered Workforce</h2>

<section class="sales" aria-label="AI agents">
  <div class="card" style="left:87px;top:1130px;width:160px;height:207px" role="img" aria-label="AI follow up reminders robot"></div>
  <div class="card face" style="left:263px;top:1105px;width:197px;height:253px" role="img" aria-label="AI lead qualifier portrait"></div>
  <div class="card" style="left:479px;top:1072px;width:247px;height:321px" role="img" aria-label="AI sales agent robot"></div>
  <div class="card light" style="left:742px;top:1105px;width:197px;height:253px" role="img" aria-label="AI receptionist robot"></div>
  <div class="card light" style="left:958px;top:1130px;width:160px;height:207px" role="img" aria-label="AI appointment setter robot"></div>
  <div class="arrow" style="left:59px;top:1230px;background:#fff;box-shadow:0 2px 8px rgba(0,0,0,.25)"><svg width="18" height="18" viewBox="0 0 18 18" fill="none" stroke="#3b13a0" stroke-width="2"><path d="M9 4L4 9l5 5M14 4L9 9l5 5"/></svg></div>
  <div class="arrow" style="left:1095px;top:1230px;background:var(--deep)"><svg width="18" height="18" viewBox="0 0 18 18" fill="none" stroke="#fff" stroke-width="2"><path d="M4 4l5 5-5 5M9 4l5 5-5 5"/></svg></div>
  <div class="arrow" style="left:564px;top:1350px;width:72px;height:72px;background:linear-gradient(135deg,var(--purple),var(--magenta),var(--orange));border:3px solid #fff"><svg width="30" height="30" viewBox="0 0 24 24" fill="none" stroke="#fff" stroke-width="2"><circle cx="12" cy="8" r="4"/><path d="M4 20a8 8 0 0116 0"/></svg></div>
  <div class="label" style="left:67px;top:1353px;width:200px">AI Follow Up Reminders</div>
  <div class="label" style="left:262px;top:1380px;width:200px;font-size:14px">AI Lead Qualifier</div>
  <div class="label" style="left:741px;top:1375px;width:200px;font-size:14px">AI Receptionist</div>
  <div class="label" style="left:938px;top:1353px;width:200px">AI Appointment Setter</div>
  <h3 class="abs center" style="top:1447px">AI SALES AGENT</h3>
  <p class="abs center copy" style="top:1489px">Milo will take your inbound sales calls. Will give all detailed<br>information to the customer, answer questions in a normal<br>conversational tone and can book sales appointments or transfer<br>hot prospects to a human to close the sale.</p>
  <a class="btn" style="top:1599px">Get An Instant Free Demo <i></i></a>
  <p class="abs center copy" style="top:1671px;color:var(--grey)">We Will Create An Ai Agent Customized For Your Business At No Cost. Simply Click The Button Above And<br>Your Very Own Ai Agent Will Be Calling You In Just A Couple Minutes. Experience The Magic And Get<br>Ready To Be Very Impressed!</p>
</section>

<section class="abs wish" aria-label="Your wish is their command">
  <div class="abs visual" role="img" aria-label="Digital profile with flowing voice waves"></div>
</section>
<h2 class="abs serif" style="left:636px;top:1900px;font-size:44px;line-height:56px;color:#fff">Your Wish Is<br>Their <span class="grad-gold">Command</span></h2>
<p class="abs wish-sub">Your New Ai Agents Will Never Call In Sick<br>And Will Never Complain!</p>
<p class="abs wish-copy">With your new team of AI Agents, handling inbound calls, sending emails and sms messages, booking appointments and handling customer service inquiries is going to save you a ton of time and money.</p>

<h2 class="abs center serif sick">An Employee That Never Gets Sick!</h2>
<div class="abs rule"></div>
<svg class="abs" style="left:0;top:2460px" width="1200" height="360" viewBox="0 0 1200 360" fill="none" stroke="#6a3cc8" stroke-width="2.5">
  <path d="M135 182A160 160 0 01440 120"/><path d="M450 120A160 160 0 01760 120"/><path d="M760 120A160 160 0 011068 182"/>
  <path d="M445 230A160 160 0 00757 230"/>
  <circle cx="135" cy="182" r="5" fill="#6a3cc8"/><circle cx="1068" cy="182" r="5" fill="#6a3cc8"/>
</svg>
<div class="orb" style="left:143px;top:2484px"><svg width="44" height="44" viewBox="0 0 24 24" fill="none" stroke="#fff" stroke-width="1.5"><path d="M9 11V5a2 2 0 014 0v6l5 1a2 2 0 011 3l-2 5H9l-4-5a2 2 0 013-2z"/></svg><h4>Trained In Seconds</h4><hr><p>Learns Your Entire Website In Seconds</p></div>
<div class="orb mid" style="left:456px;top:2484px"><svg width="44" height="44" viewBox="0 0 24 24" fill="none" stroke="#fff" stroke-width="1.5"><circle cx="12" cy="6" r="3"/><path d="M12 9v11M8 14h8M9 20h6"/></svg><h4>Worldwide</h4><hr><p>Works Anywhere In The Globe</p></div>
<div class="orb" style="left:767px;top:2484px"><svg width="44" height="44" viewBox="0 0 24 24" fill="none" stroke="#fff" stroke-width="1.5"><path d="M6 20v-5a7 7 0 1112 0l-1 5M11 8l-2 4h4l-2 4"/></svg><h4>User-Friendly</h4><hr><p>Your AI Agents Sound As If They're Real Humans</p></div>

<section class="abs hire" aria-label="Ready to be hired"></section>
<h2 class="abs center serif hire-h grad-purple">Our AI Agents Our <span class="grad-gold">Ready</span><br>To Be Hired</h2>
<p class="abs center hire-sub">Lightning-Fast Responses</p>
<p class="abs center hire-line">Instant answers, no coffee, bathroom or lunch breaks needed</p>
<p class="abs center copy" style="top:3180px;color:#fff">We Will Create An Ai Agent Customized For Your Business At No Cost. Simply Click The Button Above And<br>Your Very Own Ai Agent Will Be Calling You In Just A Couple Minutes. Experience The Magic And Get<br>Ready To Be Very Impressed!</p>
<a class="btn" style="top:3278px">Get An Instant Free Demo <i></i></a>

<h2 class="abs center serif faq-h">Do You Have Questions?</h2>
<div class="faq" style="top:3572px">WHAT EXACTLY ARE THE AI VOICE AGENTS?<b><svg width="16" height="16" viewBox="0 0 16 16" fill="none" stroke="#fff" stroke-width="2"><path d="M4 3l4 4 4-4M4 8l4 4 4-4"/></svg></b></div>
<div class="faq" style="top:3655px">HOW WILL THESE AI VOICE AGENTS BENEFIT<b><svg width="16" height="16" viewBox="0 0 16 16" fill="none" stroke="#fff" stroke-width="2"><path d="M4 3l4 4 4-4M4 8l4 4 4-4"/></svg></b></div>
<div class="faq" style="top:3738px">ARE THEY EASY TO USE?<b><svg width="16" height="16" viewBox="0 0 16 16" fill="none" stroke="#fff" stroke-width="2"><path d="M4 3l4 4 4-4M4 8l4 4 4-4"/></svg></b></div>

<section class="abs lower" aria-label="Possibilities"></section>
<div class="abs review"></div>
<h2 class="abs center" style="top:3950px;font-family:'Playfair Display',serif;font-weight:700;font-size:38px;line-height:52px;color:#fff">After Our Customers Have A<br>Conversation With Their New Ai Voice<br>Agent They Give Us 5 Stars!</h2>
<div class="abs center stars">★★★★★</div>
<div class="abs robot" role="img" aria-label="Friendly white robot mascot"></div>
<h2 class="abs center serif possible"><span class="grad-gold">These AI Agents Can Help Your Business</span><br><span class="grad-purple">Tremendously. Imagine The<br>Possibilities</span></h2>
<p class="abs center copy" style="top:4729px;color:#fff">We Will Create An Ai Agent Customized For Your Business At No Cost. Simply Click The Button Above And<br>Your Very Own Ai Agent Will Be Calling You In Just A Couple Minutes. Experience The Magic And Get<br>Ready To Be Very Impressed!</p>
<a class="btn" style="top:4829px">Get An Instant Free Demo <i></i></a>

<footer>
  <div class="brand" style="top:5017px"><div class="dot"></div><span>Brightfern Promotion Hub</span></div>
  <p class="abs center foot-text">14-Day Money Back Guarantee Terms: If you use the ai agents and you're not happy.<br>Then you can contact us in the first 14 days for a full refund.</p>
  <p class="abs center foot-links">PRIVACY | TERMS &amp; CONDITIONS | EARNINGS &amp; PRODUCTS DISCLAIMER</p>
  <div class="abs foot-rule"></div>
  <p class="abs center copyright">Copyright@2025.All Rights Reserved</p>
</footer>

</body>
</html>
```